High-end construction company needs a business card design

We need a modern looking business card that draws people in, is memorable and looks so good people will want to sick it on their fridges.
On the first side what is needed are:
Logo
My name - Tomasz Brelwik
Title - Managing Director
Website - www.varkelt.co.uk
Email - tomasz@varkelt.co.uk
Telephone - 020 5194 6281
Mobile - 07845139072
On the back side was is needed is a list of all the services we provide:
-Kitchen Renovations
-Bathroom Renovations
-House Renovations
-Garage Conversions
-Extensions
-Loft Conversions
-Conservatories
-Carpentry
-Tiling
-Electrical
-Plumbing & Heating
-Bricklaying
-Landscaping
-Decorating
-Plastering
We would like the colours to be the same shades as on the logo with grey or black for the words.
Target Market(s)
Anyone who needs building work done
Contact Information for Business Card
This business card is for a construction company which strives to deliver excellent service and quality.
The look and feel of the card should represent this.
Requirements
Must have
- On the first side what is needed are:
Logo
My name - Tomasz Brelwik
Title - Managing Director
Website - www.varkelt.co.uk
Email - tomasz@varkelt.co.uk
Telephone - 020 5194 6281
Mobile - 07845139072
Nice to have
- Cool looking features

```html
<!DOCTYPE html>
<html lang="en">
<head>
<meta charset="utf-8">
<title>Varkelt Construction Ltd – Business Card</title>
<link rel="stylesheet" href="https://fonts.googleapis.com/css2?family=Montserrat:wght@500;700;800&family=Open+Sans:wght@400&display=swap">
<style>
  :root {
    --backdrop: #e4e4e4;
    --card-dark: #2b2b2b;
    --card-light: #f4f4f4;
    --green-bright: #6cbf3f;
    --green-deep: #3f8d3b;
    --ink: #2a2a2a;
    --white: #ffffff;
  }
  * { margin: 0; padding: 0; box-sizing: border-box; }
  html, body {
    width: 1200px; height: 960px; overflow: hidden;
    background: var(--backdrop);
  }
  .canvas { position: relative; width: 1200px; height: 960px; }
  .card {
    position: absolute; left: 328px; width: 542px; height: 352px; overflow: hidden;
  }

  /* Services side */
  .card-services { top: 107px; background: var(--card-dark); }
  .service-list {
    position: absolute; left: 33px; top: 34px; list-style: none;
    font-family: "Montserrat", sans-serif; font-weight: 500;
    font-size: 15px; line-height: 22.6px; color: var(--green-bright);
  }
  .service-list .dot { color: #cfcfcf; font-size: 11px; padding: 0 2px; }
  .hero-art {
    position: absolute; left: 140px; top: 108px; width: 400px; height: 244px;
    background: linear-gradient(135deg, rgba(108,191,63,0.15) 0%, var(--green-bright) 55%, var(--green-deep) 100%);
    clip-path: polygon(0 100%, 68% 0, 100% 40%, 100% 100%);
  }

  /* Contact side */
  .card-contact { top: 500px; background: var(--card-light); }
  .brand {
    position: absolute; left: 45px; top: 100px;
    font-family: "Montserrat", sans-serif; font-weight: 800;
    color: var(--green-bright); line-height: 1;
  }
  .brand-name { display: block; font-size: 40px; letter-spacing: 0.5px; }
  .brand-sub { display: block; font-size: 11.5px; letter-spacing: 1.6px; margin-top: 6px; }
  .person {
    position: absolute; right: 41px; top: 190px; text-align: right;
    font-family: "Montserrat", sans-serif;
  }
  .person-name { font-weight: 700; font-size: 18px; color: var(--green-deep); letter-spacing: 0.3px; }
  .person-title { font-weight: 500; font-size: 15px; color: var(--ink); margin-top: 1px; }
  .accent-tab {
    position: absolute; right: 0; top: 188px; width: 13px; height: 46px; background: var(--green-bright);
  }
  .rule {
    position: absolute; left: 45px; top: 239px; width: 456px; height: 2px; background: var(--green-bright);
  }
  .contacts {
    position: absolute; left: 46px; top: 257px; list-style: none;
    font-family: "Open Sans", sans-serif; font-size: 14px; color: var(--ink); line-height: 19px;
  }
  .contacts li { display: flex; align-items: center; gap: 5px; }
  .contacts svg { width: 12px; height: 12px; fill: var(--green-deep); flex: none; }
  .band-deep {
    position: absolute; left: 0; bottom: 0; width: 340px; height: 16px; background: var(--green-deep);
  }
  .band-web {
    position: absolute; right: 0; bottom: 0; width: 215px; height: 26px; background: var(--green-bright);
    clip-path: polygon(25px 0, 100% 0, 100% 100%, 0 100%);
  }
  .website {
    position: absolute; right: 41px; bottom: 5px;
    font-family: "Open Sans", sans-serif; font-size: 13px; color: var(--white);
  }
</style>
</head>
<body>
<main class="canvas">

  <section class="card card-services" aria-label="Services side">
    <ul class="service-list">
      <li>Kitchen Renovations <span class="dot">•</span> Extensions</li>
      <li>Bathroom Renovations <span class="dot">•</span> Bricklaying</li>
      <li>House Renovations <span class="dot">•</span> Decorating</li>
      <li>Garage Conversions <span class="dot">•</span> Electrical</li>
      <li>Plumbing &amp; Heating <span class="dot">•</span> Plastering</li>
      <li>Loft Conversions <span class="dot">•</span> Landscaping</li>
      <li>Conservatories <span class="dot">•</span> Carpentry <span class="dot">•</span> Tiling</li>
    </ul>
    <div class="hero-art" role="img" aria-label="Large green illustration of an excavator arm over houses and buildings"></div>
  </section>

  <section class="card card-contact" aria-label="Contact side">
    <div class="brand">
      <span class="brand-name">VARKELT</span>
      <span class="brand-sub">CONSTRUCTION LTD</span>
    </div>

    <div class="person">
      <p class="person-name">TOMASZ BRELWIK</p>
      <p class="person-title">Managing Director</p>
    </div>
    <div class="accent-tab"></div>
    <div class="rule"></div>

    <ul class="contacts">
      <li>
        <svg viewBox="0 0 24 24" aria-hidden="true"><path d="M6.6 10.8a15.1 15.1 0 0 0 6.6 6.6l2.2-2.2c.3-.3.7-.4 1-.2 1.1.4 2.3.6 3.6.6.6 0 1 .4 1 1V20c0 .6-.4 1-1 1A17 17 0 0 1 3 4c0-.6.4-1 1-1h3.5c.6 0 1 .4 1 1 0 1.3.2 2.5.6 3.6.1.3 0 .7-.2 1z"/></svg>
        020 5194 6281
      </li>
      <li>
        <svg viewBox="0 0 24 24" aria-hidden="true"><path d="M7 1h10a2 2 0 0 1 2 2v18a2 2 0 0 1-2 2H7a2 2 0 0 1-2-2V3a2 2 0 0 1 2-2zm0 3v14h10V4zm5 15.5a1.2 1.2 0 1 0 0 2.4 1.2 1.2 0 0 0 0-2.4z"/></svg>
        07845139072
      </li>
      <li>
        <svg viewBox="0 0 24 24" aria-hidden="true"><path d="M2 5h20v14H2zm2 2v.5l8 5.5 8-5.5V7zm0 2.9V17h16V9.9l-8 5.5z"/></svg>
        tomasz@varkelt.co.uk
      </li>
    </ul>

    <div class="band-deep"></div>
    <div class="band-web"></div>
    <p class="website">www.varkelt.co.uk</p>
  </section>

</main>
</body>
</html>
```